NEW Modern Sleek Business Card for VR Language Startup

Our startup is using VR to lead the next wave of world language education. We need a two-sided business card that introduces the larger organization (Lumevra Language Inc) and our contact info on one side and shows the product, Glimwoorld, on the other side.

Side 1 (contact info)= Lumevra Logo and Contact info (name, title, phone, email)

Side 2 (product)= Glimworld logo, text, and website
Text= Culturally Immersive Language Learning Games
Website= www.glimworld-play.com

Target Market(s)

Education, Technology

Contact Information for Business Card

Contact info will be updated upon approval of the design. For now, put this as a placeholder.

Perry Dunmore
Founder & CEO
pdunmore@quillpost-mail.net
(555)-014-2286

Font styles to use
Other font styles liked:
• Gibson and Century Gothic are the brand fonts

Requirements
Nice to have
• I would love to see cohesion between the design and colors of the two logos. I have attached a few business card designs that I like, so you can get a feel for my preferred style.

```html
<!DOCTYPE html>
<html lang="en">
<head>
<meta charset="utf-8">
<title>Lumevra Language Inc – Business Card</title>
<link href="https://fonts.googleapis.com/css2?family=Montserrat:wght@500;600;700&family=Questrial&display=swap" rel="stylesheet">
<style>
  :root {
    --stage: #1d1d22;
    --card-black: #050505;
    --paper: #ffffff;
    --ink: #2f2f36;
    --ink-soft: #6b6b75;
    --cyan: #45c3e3;
    --blue: #4f7fd6;
    --violet: #6a5bb5;
    --orange: #f2762e;
    --pink: #e6336f;
    --purple: #8a3fb0;
    --product-mark: #4f6fd0;
    --brand-mark: #d83b6a;
  }
  * { box-sizing: border-box; margin: 0; padding: 0; }
  html, body {
    width: 1200px; height: 800px; overflow: hidden;
    background: var(--stage);
  }
  .canvas {
    width: 1200px; height: 800px;
    display: flex; align-items: center; justify-content: center; gap: 40px;
  }
  .card {
    position: relative; width: 540px; height: 309px;
    border-radius: 24px; overflow: hidden;
    box-shadow: 0 18px 40px rgba(0,0,0,.45);
  }

  /* Product side */
  .card--product {
    padding: 16px;
    background: linear-gradient(135deg, var(--cyan) 0%, var(--blue) 55%, var(--violet) 100%);
  }
  .product-face {
    width: 100%; height: 100%; border-radius: 16px; background: var(--paper);
    display: flex; flex-direction: column; align-items: center; justify-content: center;
    text-align: center;
  }
  .product-logo { display: flex; align-items: center; gap: 14px; margin-bottom: 18px; }
  .product-logo__dot {
    width: 44px; height: 44px; border-radius: 50%;
    background: var(--product-mark);
  }
  .product-logo__name {
    font-family: "Questrial", "Century Gothic", sans-serif;
    font-size: 46px; color: var(--product-mark); letter-spacing: .5px;
  }
  .product-tagline {
    font-family: "Montserrat", sans-serif; font-weight: 500;
    font-size: 15px; color: var(--ink); margin-bottom: 6px;
  }
  .product-url {
    font-family: "Montserrat", sans-serif; font-weight: 600;
    font-size: 14px; color: var(--ink-soft);
  }
  .product-url__name { color: var(--blue); }

  /* Contact side */
  .card--contact { background: var(--card-black); }
  .brand-panel-edge {
    position: absolute; left: 0; bottom: 0; width: 288px; height: 232px;
    border-top-right-radius: 52px;
    background: linear-gradient(160deg, var(--pink) 0%, var(--purple) 100%);
  }
  .brand-panel {
    position: absolute; left: 0; bottom: 0; width: 280px; height: 224px;
    border-top-right-radius: 46px; background: var(--paper);
    display: flex; align-items: center; justify-content: center; gap: 12px;
  }
  .brand-logo__dot {
    width: 30px; height: 30px; border-radius: 50%; background: var(--brand-mark);
  }
  .brand-logo__name {
    font-family: "Montserrat", sans-serif; font-weight: 700;
    font-size: 32px; letter-spacing: 1px; color: var(--ink);
  }
  .contact {
    position: absolute; left: 306px; top: 34px; right: 14px;
    color: var(--paper); font-family: "Montserrat", sans-serif;
  }
  .contact__name { font-weight: 700; font-size: 19px; letter-spacing: .6px; text-transform: uppercase; white-space: nowrap; }
  .contact__title {
    display: inline-block;
    font-weight: 600; font-size: 13px; margin-top: 2px;
    background: linear-gradient(90deg, var(--orange), var(--pink), var(--purple));
    -webkit-background-clip: text; background-clip: text; color: transparent;
  }
  .contact__rule {
    height: 1px; margin: 14px 0;
    background: linear-gradient(90deg, var(--pink), var(--purple));
  }
  .contact__row {
    display: flex; align-items: center; gap: 8px;
    font-size: 10.5px; font-weight: 500; white-space: nowrap;
  }
  .contact__icon {
    flex: none; width: 22px; height: 22px; border-radius: 50%;
    background: linear-gradient(135deg, var(--orange), var(--pink), var(--purple));
    display: flex; align-items: center; justify-content: center;
  }
  .contact__icon-inner {
    width: 17px; height: 17px; border-radius: 50%; background: var(--paper);
    display: flex; align-items: center; justify-content: center;
  }
  .contact__web { margin-top: 18px; font-size: 13px; font-weight: 600; white-space: nowrap; }
  .contact__web-name { color: var(--cyan); }
</style>
</head>
<body>
<main class="canvas">
  <section class="card card--product" aria-label="Product side">
    <div class="product-face">
      <div class="product-logo">
        <span class="product-logo__dot"></span>
        <span class="product-logo__name">Glimworld</span>
      </div>
      <p class="product-tagline">Culturally Immersive Language Learning Games</p>
      <p class="product-url">www.<span class="product-url__name">glimworld</span>-play.com</p>
    </div>
  </section>

  <section class="card card--contact" aria-label="Contact side">
    <div class="brand-panel-edge"></div>
    <div class="brand-panel">
      <span class="brand-logo__dot"></span>
      <span class="brand-logo__name">Lumevra</span>
    </div>
    <div class="contact">
      <p class="contact__name">Perry Dunmore</p>
      <p class="contact__title">Founder &amp; CEO</p>
      <div class="contact__rule"></div>
      <p class="contact__row">
        <span class="contact__icon"><span class="contact__icon-inner">
          <svg width="10" height="10" viewBox="0 0 24 24" aria-hidden="true"><path fill="#222" d="M6.6 10.8a15.1 15.1 0 0 0 6.6 6.6l2.2-2.2a1 1 0 0 1 1-.25 11.4 11.4 0 0 0 3.6.57 1 1 0 0 1 1 1V20a1 1 0 0 1-1 1A17 17 0 0 1 3 4a1 1 0 0 1 1-1h3.5a1 1 0 0 1 1 1c0 1.250.2 2.450.57 3.570a1 1 0 0 1-.25 1z"/></svg>
        </span></span>
        (555)-014-2286
      </p>
      <div class="contact__rule"></div>
      <p class="contact__row">
        <span class="contact__icon"><span class="contact__icon-inner">
          <svg width="10" height="10" viewBox="0 0 24 24" aria-hidden="true"><rect x="2" y="5" width="20" height="14" rx="2" fill="#222"/><path d="M3 6l9 7 9-7" stroke="#fff" stroke-width="2" fill="none"/></svg>
        </span></span>
        pdunmore@quillpost-mail.net
      </p>
      <p class="contact__web">www.<span class="contact__web-name">glimworld</span>-play.com</p>
    </div>
  </section>
</main>
</body>
</html>
```